Need Business Card ASAP

We need a business card design for a meeting coming up in a few days. The company name is Harlow Ridge Building and Construction and the logo is attached. Something clean, cool, and contemporary that we can get to a printer right away. Attached is the business card for Volmar Energy, an affiliated company, which we like. Instead of the hawk on the back, you could use the attached "D". We'll also be needing matching letterhead in the near future, so ideas for that are welcome.

```html
<!DOCTYPE html>
<html lang="en">
<head>
<meta charset="utf-8">
<title>Harlow Ridge Building and Construction – Business Card</title>
<link rel="stylesheet" href="https://fonts.googleapis.com/css2?family=Open+Sans:wght@400;600;700&display=swap">
<style>
  :root {
    --backdrop: #8a6a4a;
    --band-grey: #dcdcdc;
    --rule-grey: #d4d4d4;
    --rule-tan: #c2bc94;
    --card-white: #ffffff;
    --ink: #444444;
    --ink-dark: #2b2b2b;
    --tan-top: #b8b28a;
    --tan-bottom: #dedac6;
    --name-light: #ffffff;
  }
  * { box-sizing: border-box; margin: 0; padding: 0; }
  html, body {
    width: 1034px; height: 1200px; overflow: hidden;
    background: var(--backdrop);
    font-family: "Open Sans", Arial, sans-serif;
    color: var(--ink);
  }
  .card {
    position: absolute;
    box-shadow: 0 2px 8px rgba(0,0,0,.25);
  }
  /* Front */
  .card-front {
    left: 62px; top: 54px; width: 886px; height: 506px;
    background: var(--card-white);
  }
  .band-top, .band-bottom {
    position: absolute; left: 0; width: 100%; height: 73px;
    background: var(--band-grey);
  }
  .band-top { top: 0; }
  .band-bottom { bottom: 0; }
  .company-heading {
    position: absolute; top: 80px; left: 0; width: 100%;
    text-align: center;
  }
  .company-name { font-size: 29px; font-weight: 600; color: var(--ink); }
  .company-address { font-size: 21px; margin-top: 4px; color: var(--ink); }
  .rule {
    position: absolute; top: 162px; height: 8px;
  }
  .rule-grey { left: 0; width: 610px; background: var(--rule-grey); }
  .rule-tan { left: 620px; right: 0; background: var(--rule-tan); }
  .brand-mark {
    position: absolute; left: 34px; top: 191px; width: 171px; height: 216px;
    display: flex; flex-direction: column; align-items: center; justify-content: center;
    gap: 14px; text-align: center;
  }
  .brand-square { width: 34px; height: 34px; background: var(--rule-tan); }
  .brand-name {
    font-size: 22px; font-weight: 600; line-height: 1.2; color: var(--ink-dark);
  }
  .person {
    position: absolute; right: 81px; top: 178px; text-align: right;
  }
  .person-name { font-size: 32px; font-weight: 700; color: var(--ink); line-height: 1.1; }
  .person-title { font-size: 19px; font-weight: 700; color: var(--ink); margin-top: 4px; }
  .contacts {
    position: absolute; right: 81px; top: 274px; list-style: none; text-align: right;
  }
  .contacts li {
    font-size: 22px; line-height: 39px; color: var(--ink);
    display: flex; justify-content: flex-end; align-items: center; gap: 8px;
  }
  .contacts svg { width: 18px; height: 18px; fill: var(--ink); }
  /* Back */
  .card-back {
    left: 51px; top: 605px; width: 887px; height: 511px;
    background: linear-gradient(to bottom, var(--tan-top), var(--tan-bottom));
  }
  .back-name {
    position: absolute; left: 0; top: 190px; width: 100%; text-align: center;
    font-size: 52px; font-weight: 700; color: var(--name-light); line-height: 1.2;
  }
  .back-url {
    position: absolute; left: 0; top: 452px; width: 100%; text-align: center;
    font-size: 27px; font-weight: 700; letter-spacing: 2px; color: var(--ink);
  }
</style>
</head>
<body>
  <section class="card card-front">
    <div class="band-top"></div>
    <header class="company-heading">
      <p class="company-name">Harlow Ridge Building and Construction</p>
      <p class="company-address">00, Complex Name, Street, City 00000</p>
    </header>
    <div class="rule rule-grey"></div>
    <div class="rule rule-tan"></div>

    <div class="brand-mark">
      <span class="brand-square"></span>
      <span class="brand-name">Harlow Ridge</span>
    </div>

    <div class="person">
      <p class="person-name">Your Name</p>
      <p class="person-title">Title</p>
    </div>

    <ul class="contacts">
      <li>
        <svg viewBox="0 0 24 24" aria-hidden="true"><path d="M6.6 10.8a15 15 0 0 0 6.6 6.6l2.2-2.2a1 1 0 0 1 1-.25 11.4 11.4 0 0 0 3.6.57 1 1 0 0 1 1 1V20a1 1 0 0 1-1 1A17 17 0 0 1 3 4a1 1 0 0 1 1-1h3.5a1 1 0 0 1 1 1c0 1.25.2 2.45.57 3.57a1 1 0 0 1-.25 1z"/></svg>
        (123) 456-7890
      </li>
      <li>
        <svg viewBox="0 0 24 24" aria-hidden="true"><path d="M8 1h8a2 2 0 0 1 2 2v18a2 2 0 0 1-2 2H8a2 2 0 0 1-2-2V3a2 2 0 0 1 2-2zm0 3v13h8V4zm4 15a1 1 0 1 0 0 2 1 1 0 0 0 0-2z"/></svg>
        (123) 456-7890
      </li>
      <li>
        <svg viewBox="0 0 24 24" aria-hidden="true"><path d="M2 6h20v12H2zm2 2v.5l8 5 8-5V8l-8 5z"/></svg>
        yourname@harlowridgebuild.com
      </li>
      <li>
        <svg viewBox="0 0 24 24" aria-hidden="true"><path d="M12 2a10 10 0 1 0 0 20 10 10 0 0 0 0-20zm6.9 9h-3a15 15 0 0 0-1.3-5.6A8 8 0 0 1 18.9 11zM12 4c.9 1.2 1.8 3.6 1.9 7h-3.8c.1-3.4 1-5.8 1.9-7zM9.4 5.4A15 15 0 0 0 8.1 11h-3a8 8 0 0 1 4.3-5.6zM5.1 13h3a15 15 0 0 0 1.3 5.6A8 8 0 0 1 5.1 13zm6.9 7c-.9-1.2-1.8-3.6-1.9-7h3.8c-.1 3.4-1 5.8-1.9 7zm2.6-1.4a15 15 0 0 0 1.3-5.6h3a8 8 0 0 1-4.3 5.6z"/></svg>
        www.harlowridgebuild.com
      </li>
    </ul>
    <div class="band-bottom"></div>
  </section>

  <section class="card card-back">
    <p class="back-name">Harlow Ridge</p>
    <p class="back-url">www.harlowridgebuild.com</p>
  </section>
</body>
</html>
```